Company that sells high quality boat cleaning supplies needs new Homepage Design

We need a homepage design for a company that sells high quality boat cleaning and maintanence products. This company is called VPX61. There are 3 primary products; a soap for boats, waterless wash & Wax, and a Ceramic Spray coating and protectant.

Current Website: https://vpx61.com/

Customer Avatar/ Core Message Canvas: https://sheets.tarvolin.net/s/7qWk2Lp9RbXe4TnHy8MfC3uZaD1oJv6GsKxE5iBtN0Ph/view?share=open

Homepage Template: https://sheets.tarvolin.net/d/4Hb8nYc2QwLe6RkT0vMxJ5aPfZ9uGtSoDi3Ck7EyBn1V/view?share=open

There is info on imagery in the homepage template. Where there isn't, appropriate stock imagery is acceptable.

Logo Design and Slogan images: https://vault.tarvolin.net/f/9kLmQ2rTz8WyHn4PcVb6XeJ0gA5sDu7?share=open

Product Images: https://vault.tarvolin.net/f/3pNcR7wYh1KeTm8ZsVa4QbLu6Dj9Fgx?share=open

```html
<!DOCTYPE html>
<html lang="en">
<head>
<meta charset="utf-8">
<title>VPX61 — Stress-Free Boat Care</title>
<link href="https://fonts.googleapis.com/css2?family=Poppins:wght@400;500;600;700&display=swap" rel="stylesheet">
<style>
:root{
  --ink:#111111;
  --white:#ffffff;
  --blue:#5879ab;
  --blue-btn:#5b7db4;
  --pale-blue:#c2d5e6;
  --dark:#1f1f1f;
  --card:#1a1a1a;
  --grey:#dcdcdc;
  --line:#b9b9b9;
  --play:#e63946;
  --link:#3a9bd9;
}
*{box-sizing:border-box;margin:0;padding:0}
html,body{width:1200px;height:4275px;overflow:hidden}
body{font-family:"Poppins",sans-serif;color:var(--ink);background:var(--white);position:relative}
section,header,footer{position:relative;width:1200px}
.abs{position:absolute}

/* header */
.site-header{height:86px;border-bottom:3px solid var(--grey)}
.brand{left:113px;top:14px;font-size:44px;font-weight:600;letter-spacing:-1px;line-height:1}
.nav{left:393px;top:28px;display:flex;gap:58px;font-size:22px}
.nav a{color:var(--ink);text-decoration:none}
.nav .active{font-weight:600;border-bottom:2px solid var(--ink)}
.login{left:922px;top:22px;width:97px;height:38px;background:var(--blue-btn);color:#fff;font-size:13px;font-weight:600;display:flex;align-items:center;justify-content:center;border-radius:3px}
.cart{left:1038px;top:20px;width:46px;height:46px;border-radius:50%;background:var(--blue-btn);display:flex;align-items:center;justify-content:center}

/* hero */
.hero{height:514px;background:linear-gradient(120deg,#0f4f55 0%,#1d6e72 45%,#0e4a52 100%)}
.hero-title{left:600px;top:95px;width:520px;color:#fff;font-size:27px;font-weight:700;line-height:48px}
.hero-list{left:600px;top:252px;color:#fff;font-size:14px;font-weight:600;list-style:none;line-height:38px}
.btn-outline{border:2px solid #fff;color:#fff;font-size:14px;font-weight:600;display:flex;align-items:center;justify-content:center}
.btn-fill{background:var(--blue-btn);border:2px solid #8fa9d1;color:#fff;font-size:14px;font-weight:600;display:flex;align-items:center;justify-content:center}

/* trust */
.trust{height:323px;background:var(--pale-blue)}
.trust h2{position:absolute;top:52px;width:100%;text-align:center;font-size:30px;font-weight:700}
.badge{top:203px;width:188px;height:53px;background:#fff;border-radius:4px;font-size:14px;display:flex;align-items:flex-end;justify-content:center;text-align:center;padding-bottom:8px;line-height:16px}
.badge-icon{top:140px;width:80px;height:80px;border-radius:50%;background:#fff;border-right:4px solid #555;display:flex;align-items:center;justify-content:center}

/* products */
.product{height:507px}
.product.blue{background:var(--blue)}
.product.dark{background:var(--dark)}
.shot{top:78px;width:358px;height:358px;border-radius:50%;border:4px solid #fff;overflow:hidden;background:#000}
.shot .bottle{position:absolute;left:129px;top:30px;width:100px;height:300px;border-radius:14px}
.shot .play{position:absolute;left:150px;top:150px;width:56px;height:56px;border-radius:50%;background:var(--play);display:flex;align-items:center;justify-content:center}
.product-card{top:161px;width:489px;height:188px;background:var(--card);border:2px solid #555;border-radius:14px;color:#fff;text-align:center}
.product-card h3{font-size:26px;font-weight:600;line-height:38px}
.cart-btn{width:181px;height:50px;border:2px solid #fff;color:#fff;font-size:15px;font-weight:600;display:flex;align-items:center;justify-content:center;margin:0 auto}

/* solution */
.solution{height:977px}
.solution h2{position:absolute;top:80px;width:100%;text-align:center;font-size:34px;font-weight:700}
.solution .sub{position:absolute;top:143px;width:100%;text-align:center;font-size:20px;font-weight:600}
.faq-box{left:111px;top:216px;width:978px;height:599px;border:2px solid var(--line);box-shadow:0 2px 4px rgba(0,0,0,.15)}
.faq-item{left:32px;width:914px;height:88px;border:1.5px solid var(--line);border-radius:0 44px 44px 0;display:flex;align-items:center;padding-left:40px;font-size:21px;font-weight:600}
.faq-item::before{content:"";width:9px;height:9px;border-radius:50%;background:var(--ink);margin-right:21px}
.faq-toggle{position:absolute;right:40px;top:20px;width:48px;height:48px;border-radius:50%;border:1.5px solid #888;display:flex;align-items:center;justify-content:center}
.faq-answer{left:32px;top:124px;width:914px;height:214px;border:1.5px solid var(--line);border-radius:0 44px 44px 0;padding:22px 26px 0 20px;font-size:17.5px;line-height:36px}
.blog-btn{left:453px;top:869px;width:291px;height:50px;border:2px solid #888;font-size:15px;font-weight:600;display:flex;align-items:center;justify-content:center}

/* community */
.community{height:428px;background:var(--grey);text-align:center}
.community h2{position:absolute;top:58px;width:100%;font-size:34px;font-weight:700;line-height:58px}
.community p{position:absolute;top:193px;width:100%;font-size:20px;line-height:33px}
.email{left:375px;top:297px;width:314px;height:65px;background:#fff;font-size:21px;padding-left:50px;display:flex;align-items:center}
.submit{left:689px;top:297px;width:134px;height:65px;background:#fff;border:2px solid #888;font-size:20px;font-weight:600;display:flex;align-items:center;justify-content:center}

/* footer */
.site-footer{height:427px}
.foot-brand{left:113px;top:110px;font-size:48px;font-weight:600;letter-spacing:-1px;line-height:1}
.foot-col{top:118px}
.foot-col h4{font-size:20px;font-weight:600;margin-bottom:32px}
.foot-col li{list-style:none;font-size:21px;line-height:33px}
.foot-links{top:333px;width:100%;display:flex;justify-content:center;gap:48px;font-size:15px}
.foot-links a{color:var(--link)}
.copy{top:390px;width:100%;text-align:center;font-size:15px}
</style>
</head>
<body>

<header class="site-header">
  <div class="abs brand">VPX61</div>
  <nav class="abs nav">
    <a class="active">Home</a><a>Blog</a><a>Contact</a><a>Shop VPX61</a>
  </nav>
  <div class="abs login">LOGIN</div>
  <div class="abs cart">
    <svg width="26" height="24" viewBox="0 0 26 24" fill="none" stroke="#fff" stroke-width="1.8"><path d="M1 2h4l3 13h13l3-9H7"/><circle cx="10" cy="20" r="2"/><circle cx="19" cy="20" r="2"/></svg>
  </div>
</header>

<section class="hero">
  <div class="abs" role="img" aria-label="Aerial photo of a white motor yacht cruising on teal sea water" style="left:0;top:0;width:600px;height:514px;background:radial-gradient(ellipse at 35% 75%,#4c8a8e 0%,rgba(15,79,85,0) 55%)"></div>
  <h1 class="abs hero-title">STRESS-FREE BOAT CARE: VPX61 TAKES THE HARD WORK OUT OF CLEANING &amp; DETAILING</h1>
  <ul class="abs hero-list">
    <li>• ECO Friendly</li><li>• Simple Application</li><li>• Advanced Nanotechnolgies</li>
  </ul>
  <div class="abs btn-outline" style="left:600px;top:379px;width:181px;height:50px">OUR BLOG</div>
  <div class="abs btn-fill" style="left:805px;top:379px;width:181px;height:50px">SHOP VPX61</div>
</section>

<section class="trust">
  <h2>START TRUST/AUTHORITY</h2>
  <div class="abs badge" style="left:113px">Simple Application</div>
  <div class="abs badge" style="left:310px">Made in the USA</div>
  <div class="abs badge" style="left:506px">eco friendly</div>
  <div class="abs badge" style="left:702px">Designed for any<br>conditions</div>
  <div class="abs badge" style="left:898px">Works the First Time</div>
  <div class="abs badge-icon" style="left:163px"><svg width="40" height="40" viewBox="0 0 40 40" fill="none" stroke="#333" stroke-width="1.6"><rect x="9" y="5" width="22" height="30"/><path d="M13 20h14M13 25h14M13 30h10"/><circle cx="20" cy="12" r="3"/></svg></div>
  <div class="abs badge-icon" style="left:360px"><svg width="40" height="40" viewBox="0 0 40 40" fill="none" stroke="#333" stroke-width="1.6"><circle cx="20" cy="20" r="15"/><circle cx="20" cy="20" r="10"/></svg></div>
  <div class="abs badge-icon" style="left:556px"><svg width="40" height="40" viewBox="0 0 40 40" fill="none" stroke="#333" stroke-width="1.6"><path d="M20 22V12M20 14c-6 0-8-4-8-8 5 0 8 3 8 8zM20 14c6 0 8-4 8-8-5 0-8 3-8 8z"/><path d="M5 28c6-4 10 2 15 0s8-4 14-2"/></svg></div>
  <div class="abs badge-icon" style="left:752px"><svg width="40" height="40" viewBox="0 0 40 40" fill="none" stroke="#333" stroke-width="1.6"><rect x="6" y="8" width="28" height="20"/><path d="M3 32h34M16 22l10-10"/></svg></div>
  <div class="abs badge-icon" style="left:948px"><svg width="40" height="40" viewBox="0 0 40 40" fill="none" stroke="#333" stroke-width="1.6"><circle cx="15" cy="12" r="5"/><path d="M6 30c0-7 4-10 9-10s9 3 9 10"/><rect x="22" y="18" width="14" height="10"/><path d="M4 32h34"/></svg></div>
</section>

<section class="product blue">
  <div class="abs shot" style="left:173px">
    <div class="bottle" role="img" aria-label="VPX61 Waterless Wash &amp; Wax spray bottle" style="background:linear-gradient(180deg,#e8e8e8 0%,#ffffff 45%,#6fcfa8 100%)"></div>
    <div class="play"><svg width="22" height="24" viewBox="0 0 22 24"><path d="M3 2l17 10L3 22z" fill="#fff"/></svg></div>
  </div>
  <div class="abs product-card" style="left:600px">
    <h3 style="margin-top:40px">Waterless Wash &amp; Wax</h3>
    <div class="cart-btn" style="margin-top:23px">ADD TO CART</div>
  </div>
</section>

<section class="product dark">
  <div class="abs product-card" style="left:110px">
    <h3 style="margin-top:26px">Graphene Ceramic Spray<br>Coating and Protectant</h3>
    <div class="cart-btn" style="margin-top:14px">ADD TO CART</div>
  </div>
  <div class="abs shot" style="left:661px">
    <div class="bottle" role="img" aria-label="VPX61 Graphene Ceramic Spray bottle" style="background:linear-gradient(180deg,#777 0%,#e6e6e6 40%,#d0d0d0 100%)"></div>
    <div class="play"><svg width="22" height="24" viewBox="0 0 22 24"><path d="M3 2l17 10L3 22z" fill="#fff"/></svg></div>
  </div>
</section>

<section class="product blue">
  <div class="abs shot" style="left:181px">
    <div class="bottle" role="img" aria-label="VPX61 Pink Soap for boats bottle" style="background:linear-gradient(180deg,#222 0%,#ff3b6b 25%,#fff 50%,#ff3b6b 100%)"></div>
    <div class="play"><svg width="22" height="24" viewBox="0 0 22 24"><path d="M3 2l17 10L3 22z" fill="#fff"/></svg></div>
  </div>
  <div class="abs product-card" style="left:600px">
    <h3 style="margin-top:40px">Pink Soap For Boats</h3>
    <div class="cart-btn" style="margin-top:23px">ADD TO CART</div>
  </div>
</section>

<section class="solution">
  <h2>THE VPX61 SOLUTION</h2>
  <p class="sub">Cleaning Products that Work The First Time!</p>
  <div class="abs faq-box">
    <div class="abs faq-item" style="top:24px">What’s the Best Boat Wax?
      <span class="faq-toggle" style="border-color:#ddd;box-shadow:0 1px 4px rgba(0,0,0,.2)"><svg width="26" height="14" viewBox="0 0 26 14" fill="none" stroke="#333" stroke-width="1.6"><path d="M1 1l12 12L25 1"/></svg></span>
    </div>
    <div class="abs faq-answer">We feel that a well-formulated, properly applied sprayable ceramic protectant is the easiest and most cost-effective way to protect and maintain the beauty of your boat’s paint or gel coat. VPX61 Graphene Spray Protectant will provide up to one year of protection in favorable conditions and is easier than applying wax or sealers. This product can be used in direct sunlight on a hot surface and layered without issues.</div>
    <div class="abs faq-item" style="top:368px">Why Use a Waterless Wash &amp; Wax?
      <span class="faq-toggle"><svg width="24" height="24" viewBox="0 0 24 24" stroke="#333" stroke-width="1.6"><path d="M12 2v20M2 12h20"/></svg></span>
    </div>
    <div class="abs faq-item" style="top:479px">What Should I Wash My Boat With?
      <span class="faq-toggle"><svg width="24" height="24" viewBox="0 0 24 24" stroke="#333" stroke-width="1.6"><path d="M12 2v20M2 12h20"/></svg></span>
    </div>
  </div>
  <div class="abs blog-btn">READ OUR BLOG FOR MORE</div>
</section>

<section class="community">
  <h2>JOIN OUR COMMUNITY: EXCLUSIVE DEALS, TIPS, AND<br>UPDATES STRAIGHT TO YOUR INBOX</h2>
  <p>Join today &amp; stay up-to-date on new product releases, shop promotions,<br>and our archery newsletters</p>
  <div class="abs email">Email</div>
  <div class="abs submit">SUBMIT</div>
</section>

<footer class="site-footer">
  <div class="abs foot-brand">VPX61</div>
  <div class="abs foot-col" style="left:395px">
    <h4>QUICK LINKS</h4>
    <ul><li>Home</li><li>Blog</li><li>Shop vpx61</li><li>Contact</li></ul>
  </div>
  <div class="abs foot-col" style="left:609px">
    <h4>OTHER LINKS</h4>
    <ul><li>Terms of Service,</li><li>Privacy Policy,</li><li>Expanded navigation</li></ul>
  </div>
  <div class="abs foot-col" style="left:868px">
    <h4>CONTACT US</h4>
    <ul><li>12 Dock Lane, BV -7810</li><li>info@vpx61.in</li><li>5550143210</li></ul>
  </div>
  <div class="abs foot-links"><a>Flagship content/case studies</a><a>Social properties</a><a>Miscellaneous information.</a></div>
  <div class="abs copy">CopyRight@2023Harborline Studio. All Right Reserved</div>
</footer>

</body>
</html>
```